Breakfast Cafe - The Sunny Nook

It is for my breakfast and lunch cafe with a hawaiian / beach theme. I am open 7 days a week from 7am to 2pm. We serve traditional American food such as omelettes, pancakes, burgers and sandwiches. I'll upload my old card and my new logo to be used. We have a lot of day to day regulars who eat there during the week, our t-shirts actually say 'Locals Only' on them. Hope this helps. Thanks.

Target Market(s)

anyone who has an appetite!

Industry/Entity Type

American Restaurant

Contact Information for Business Card

4815C Marlow Grove Avenue
Long Beach, California
(555) 731-2294

Requirements
Must have
• Address and phone number easily readable.
Nice to have
• beach or tropical theme

```html
<!DOCTYPE html>
<html lang="en">
<head>
<meta charset="utf-8">
<title>The Sunny Nook – Business Card</title>
<link rel="stylesheet" href="https://fonts.googleapis.com/css2?family=Lato:wght@400;700;900&display=swap">
<style>
  :root {
    --stage: #232323;
    --card-orange: #c4680f;
    --card-orange-deep: #a9560a;
    --card-orange-glow: #d98a2e;
    --card-light: #eeeeee;
    --text-light: #ffffff;
    --text-dark: #111111;
    --brand-blue: #3fb3d6;
    --wood: #8a4a12;
    --wood-dark: #5a2e08;
  }
  * { margin: 0; padding: 0; box-sizing: border-box; }
  html, body {
    width: 1064px; height: 1200px; overflow: hidden;
    background: var(--stage);
    font-family: "Lato", Arial, sans-serif;
  }
  .canvas { position: relative; width: 1064px; height: 1200px; }

  .card {
    position: absolute;
    width: 630px; height: 390px;
    box-shadow: 4px 5px 6px rgba(0,0,0,.55);
    overflow: hidden;
  }
  .card--front {
    left: 265px; top: 141px;
    border-radius: 0 195px 195px 0;
    background: var(--card-orange);
    color: var(--text-light);
  }
  .card--back {
    left: 234px; top: 584px;
    border-radius: 195px 0 0 195px;
    background: var(--card-light);
    color: var(--text-dark);
  }

  .front-artwork {
    position: absolute; inset: 0;
    background:
      radial-gradient(ellipse 220px 240px at 500px 200px, var(--card-orange-glow) 0%, rgba(217,138,46,0) 70%),
      radial-gradient(ellipse 180px 200px at 90px 90px, rgba(169,86,10,.55) 0%, rgba(169,86,10,0) 70%);
    opacity: .8;
  }

  .front-content { position: absolute; left: 28px; top: 46px; }
  .brand-name {
    font-weight: 900; font-size: 52px; line-height: 1;
    letter-spacing: .5px;
  }
  .tagline { margin-top: 32px; font-size: 28px; line-height: 1; }
  .contact { margin-top: 16px; font-size: 22px; line-height: 28px; }
  .contact__phone { display: flex; align-items: center; gap: 8px; font-size: 23px; }
  .contact__phone svg { width: 20px; height: 20px; fill: var(--text-light); }
  .hours { margin-top: 30px; font-size: 26px; font-weight: 700; }

  .back-mark {
    position: absolute; left: 68px; top: 60px;
    width: 246px; text-align: center;
  }
  .back-mark__disc {
    width: 228px; height: 228px; margin: 0 auto;
    border-radius: 50%;
    background: radial-gradient(circle, #f3a93f 0%, #e58c26 60%, var(--wood) 62%, var(--wood-dark) 100%);
  }
  .back-mark__name {
    margin-top: 10px;
    font-size: 32px; font-weight: 900; color: var(--brand-blue);
    white-space: nowrap;
  }

  .menu-list {
    position: absolute; right: 30px; top: 148px;
    list-style: none; text-align: right;
    font-size: 22px; line-height: 33px;
  }
  .menu-list li { display: flex; align-items: center; justify-content: flex-end; gap: 7px; }
  .menu-list li::after {
    content: ""; width: 14px; height: 14px; border-radius: 50%;
    background: linear-gradient(90deg, var(--wood-dark), var(--wood), var(--wood-dark));
  }
</style>
</head>
<body>
<main class="canvas">

  <section class="card card--front">
    <div class="front-artwork" role="img" aria-label="Faint tiki figure, torch and wave illustration in orange tones"></div>
    <div class="front-content">
      <h1 class="brand-name">The Sunny Nook</h1>
      <p class="tagline">Family owned and operated!</p>
      <div class="contact">
        <p class="contact__phone">
          <svg viewBox="0 0 24 24" aria-hidden="true"><path d="M6.6 10.8a15.1 15.1 0 0 0 6.6 6.6l2.2-2.2c.3-.3.7-.4 1-.2 1.1.4 2.3.6 3.6.6.6 0 1 .4 1 1V20c0 .6-.4 1-1 1A17 17 0 0 1 3 4c0-.6.4-1 1-1h3.5c.6 0 1 .4 1 1 0 1.3.2 2.5.6 3.6.1.3 0 .7-.2 1z"/></svg>
          (555) 731-2294
        </p>
        <p>4815C Marlow Grove Avenue</p>
        <p>Long Beach, California</p>
      </div>
      <p class="hours">Breakfast &amp; Lunch 7am - 2pm Daily</p>
    </div>
  </section>

  <section class="card card--back">
    <div class="back-mark">
      <div class="back-mark__disc" role="img" aria-label="Beach scene badge with palm tree, sunset and ship"></div>
      <p class="back-mark__name">The Sunny Nook</p>
    </div>
    <ul class="menu-list">
      <li>Omelettes</li>
      <li>Pancakes</li>
      <li>Burgers</li>
      <li>Sandwiches</li>
    </ul>
  </section>

</main>
</body>
</html>
```